MRT Property - Business Cards

Looking for a business card & general letterhead, signage etc design for our new logo.

Colours:
000a20
0056a2
00b5ef
0088ce
68cef2

Fonts:
Poppins
Karla

Please keep look and feel of new brand - example in the zip package I sent.

```html
<!DOCTYPE html>
<html lang="en">
<head>
<meta charset="utf-8">
<title>MRT Property – Business Cards</title>
<link rel="stylesheet" href="https://fonts.googleapis.com/css2?family=Poppins:wght@400;500;700&display=swap">
<style>
  :root {
    --navy: #000a20;
    --card: #0b1120;
    --blue: #0056a2;
    --cyan: #00b5ef;
    --mid: #0088ce;
    --sky: #68cef2;
    --stage: #232323;
    --white: #ffffff;
    --haze: #4a4d58;
  }
  * { margin: 0; padding: 0; box-sizing: border-box; }
  html, body { width: 1200px; height: 781px; overflow: hidden; }
  body { background: var(--stage); font-family: "Poppins", sans-serif; position: relative; }

  .card {
    position: absolute;
    width: 520px; height: 300px;
    border-radius: 28px;
    background: var(--card);
    box-shadow: 0 4px 0 var(--cyan), 0 18px 30px rgba(0,0,0,.55);
    overflow: hidden;
  }

  /* back of card */
  .card--back { left: 60px; top: 90px; }
  .back-artwork {
    position: absolute; inset: 0;
    background: linear-gradient(125deg, var(--haze) 0%, #262a36 35%, var(--card) 65%);
  }

  /* front of card */
  .card--front { left: 620px; top: 390px; }
  .brand {
    position: absolute; left: 26px; top: 122px;
    display: flex; align-items: center; gap: 10px;
  }
  .brand-dot { width: 22px; height: 22px; border-radius: 50%; background: var(--mid); }
  .brand-name { font-weight: 700; font-size: 24px; color: var(--blue); white-space: nowrap; }

  .divider {
    position: absolute; left: 258px; top: 40px;
    width: 1px; height: 160px; background: var(--mid);
  }

  .contact { position: absolute; left: 278px; top: 40px; color: var(--white); }
  .person-name { font-weight: 700; font-size: 22px; color: var(--blue); line-height: 1.1; }
  .person-title { font-size: 13px; margin-top: 4px; }
  .contact-list { list-style: none; margin-top: 20px; font-size: 12.5px; line-height: 1.75; }
  .contact-list li { display: flex; align-items: center; gap: 8px; white-space: nowrap; }
  .contact-list svg { width: 12px; height: 12px; flex: none; }

  .address-band {
    position: absolute; left: 0; right: 0; top: 226px; height: 28px;
    background: var(--cyan);
    color: var(--white); font-size: 13px;
    display: flex; align-items: center; justify-content: center;
  }
  .band-dot {
    position: absolute; right: 26px; top: 6px;
    width: 16px; height: 16px; border-radius: 50%; background: var(--navy);
  }
  .bottom-stripe {
    position: absolute; left: 0; right: 0; top: 268px; height: 10px;
    background: var(--cyan);
  }
</style>
</head>
<body>

  <section class="card card--back">
    <div class="back-artwork" role="img" aria-label="Large brand mark artwork area"></div>
  </section>

  <section class="card card--front">
    <div class="brand">
      <span class="brand-dot"></span>
      <span class="brand-name">MRT Property</span>
    </div>

    <div class="divider"></div>

    <div class="contact">
      <h1 class="person-name">DANIEL HALE</h1>
      <p class="person-title">Managing Director</p>
      <ul class="contact-list">
        <li>
          <svg viewBox="0 0 12 12"><path d="M2.5 1h2l1 3-1.5 1a7 7 0 0 0 3 3l1-1.5 3 1v2a1 1 0 0 1-1 1A10 10 0 0 1 1.5 2a1 1 0 0 1 1-1z" fill="var(--cyan)"/></svg>
          123 456 789
        </li>
        <li>
          <svg viewBox="0 0 12 12"><rect x="1" y="2.5" width="10" height="7" rx="1" fill="none" stroke="var(--cyan)" stroke-width="1.2"/><path d="M1.5 3l4.5 3.5L10.5 3" fill="none" stroke="var(--cyan)" stroke-width="1.2"/></svg>
          info@mrtproperty.com
        </li>
        <li>
          <svg viewBox="0 0 12 12"><circle cx="6" cy="6" r="5" fill="none" stroke="var(--cyan)" stroke-width="1.2"/><ellipse cx="6" cy="6" rx="2.2" ry="5" fill="none" stroke="var(--cyan)" stroke-width="1"/><path d="M1 6h10" stroke="var(--cyan)" stroke-width="1"/></svg>
          www.mrtproperty.com
        </li>
      </ul>
    </div>

    <div class="address-band">
      Your address, City State, Zip 1234
      <span class="band-dot"></span>
    </div>
    <div class="bottom-stripe"></div>
  </section>

</body>
</html>
```